"Show Times" Poster for Stunt Show

I need a fairly simple 24"x 36" poster made. I'm a professional mountain bike stunt rider and I need a poster to put on a sandwich board to display my showtimes for people walking by. The top of the poster will say: Mountain Bike (Trials) Stunt Show This text will be centered at the top BUT I want the "(Trials)" to be slightly crooked and a bit opaque with a stamped-looking font and overlap the other words just slightly. Hopefully that makes sense. Somewhere in the middle will be a photoshopped picture of me doing a stunt on my bike. The bottom will have a blank white space titled, "Show Times:" that I can write my showtimes inside of. I've attached a wildly crude and poor drawing of the basic concept. Remember, this is for a stunt show so it must look cool and have some rad colors and design... but also be simple. I will provide a picture of myself riding to be used in the poster. It will take up the middle third.

Target Market(s)

Families, Parents, Kids, general public, mountain bike enthusiastss

Industry/Entity Type

Entertainment Industry

Font styles to use
Sans Serif

Colors

Designer to choose colors to be used in the design.

Requirements
Must have
• A blank, rectangular, white space on the bottom for Show times Labelled "Show Times:"
Nice to have
• I'd like background of the whole poster to be relatively black with cool subtle graphics.

```html
<!DOCTYPE html>
<html lang="en">
<head>
<meta charset="utf-8">
<title>Mountain Bike Stunt Show – Show Times Poster</title>
<link href="https://fonts.googleapis.com/css2?family=Caprasimo&family=Black+Ops+One&display=swap" rel="stylesheet">
<style>
  :root {
    --page: #ffffff;
    --poster-black: #0b0b0b;
    --poster-charcoal: #2a2a2a;
    --ink-white: #ffffff;
    --ink-black: #000000;
    --photo-light: #d9dde2;
    --photo-mid: #8d949c;
    --photo-dark: #3e4650;
    --shadow: rgba(0,0,0,0.18);
  }
  html, body {
    margin: 0;
    padding: 0;
    width: 1200px;
    height: 1000px;
    overflow: hidden;
    background: var(--page);
  }
  .canvas {
    position: relative;
    width: 1200px;
    height: 1000px;
  }
  .poster {
    position: absolute;
    left: 287px;
    top: 12px;
    width: 657px;
    height: 965px;
    border-radius: 6px;
    overflow: hidden;
    background:
      linear-gradient(160deg, var(--poster-charcoal) 0%, var(--poster-black) 25%, var(--poster-charcoal) 45%, var(--poster-black) 65%, var(--poster-charcoal) 85%, var(--poster-black) 100%);
    box-shadow: 30px 20px 60px var(--shadow);
  }
  .texture {
    position: absolute;
    inset: 0;
    background: repeating-linear-gradient(-28deg, rgba(255,255,255,0.03) 0 30px, rgba(0,0,0,0.25) 30px 60px);
  }
  .title {
    position: absolute;
    left: 0;
    top: 0;
    width: 657px;
    height: 220px;
    margin: 0;
  }
  .title svg {
    display: block;
    width: 657px;
    height: 220px;
  }
  .title-line {
    font-family: "Caprasimo", Georgia, serif;
    font-weight: 400;
    fill: var(--ink-white);
  }
  .title-stamp {
    font-family: "Black Ops One", Impact, sans-serif;
    fill: var(--ink-white);
    stroke: var(--ink-black);
    stroke-width: 3px;
    paint-order: stroke fill;
    opacity: 0.92;
  }
  .rider-figure {
    position: absolute;
    background: linear-gradient(135deg, #f2f2f2, #bfbfbf);
    border-radius: 40%;
  }
  .rider-figure--left { left: 98px; top: 228px; width: 110px; height: 100px; }
  .rider-figure--right { left: 450px; top: 233px; width: 76px; height: 90px; }
  .star { position: absolute; width: 34px; height: 34px; }
  .star--left { left: 96px; top: 324px; }
  .star--right { left: 525px; top: 324px; }
  .hero-photo {
    position: absolute;
    left: 122px;
    top: 234px;
    width: 398px;
    height: 398px;
    border-radius: 50%;
    border: 6px solid var(--ink-white);
    background: radial-gradient(circle at 45% 30%, var(--photo-light) 0%, var(--photo-mid) 55%, var(--photo-dark) 100%);
  }
  .times-band {
    position: absolute;
    left: 6px;
    top: 590px;
    width: 590px;
    height: 100px;
  }
  .times-label {
    position: absolute;
    left: 22px;
    top: 622px;
    margin: 0;
    font-family: "Caprasimo", Georgia, serif;
    font-weight: 400;
    font-size: 42px;
    font-style: italic;
    line-height: 1;
    color: var(--ink-white);
    -webkit-text-stroke: 2.5px var(--ink-black);
    paint-order: stroke fill;
    text-shadow: 2px 2px 0 var(--ink-black);
    letter-spacing: 1px;
  }
  .times-box {
    position: absolute;
    left: 6px;
    top: 717px;
    width: 645px;
    height: 217px;
    background: var(--ink-white);
  }
</style>
</head>
<body>
<div class="canvas">
  <section class="poster">
    <div class="texture" role="img" aria-label="Subtle dark brush-stroke background texture"></div>

    <h1 class="title" aria-label="Mountain Bike (Trials) Stunt Show">
      <svg viewBox="0 0 657 220" aria-hidden="true">
        <text class="title-line" x="118" y="124" font-size="96" textLength="457" lengthAdjust="spacingAndGlyphs">Mountain Bike</text>
        <text class="title-line" x="51" y="203" font-size="84" textLength="352" lengthAdjust="spacingAndGlyphs">Stunt Show</text>
        <text class="title-stamp" x="0" y="0" font-size="40" textLength="186" lengthAdjust="spacingAndGlyphs" transform="translate(414 176) rotate(5)">(TRIALS)</text>
      </svg>
    </h1>

    <div class="rider-figure rider-figure--left" role="img" aria-label="White silhouette of a cyclist"></div>
    <div class="rider-figure rider-figure--right" role="img" aria-label="White silhouette of a cyclist"></div>

    <svg class="star star--left" viewBox="0 0 24 24" aria-hidden="true">
      <polygon points="12,1 15,9 23,9 16.5,14 19,22 12,17 5,22 7.5,14 1,9 9,9" fill="#ffffff"/>
    </svg>
    <svg class="star star--right" viewBox="0 0 24 24" aria-hidden="true">
      <polygon points="12,1 15,9 23,9 16.5,14 19,22 12,17 5,22 7.5,14 1,9 9,9" fill="#ffffff"/>
    </svg>

    <div class="hero-photo" role="img" aria-label="Photo of the rider on a trials bike mid-stunt in an indoor arena with spectators"></div>

    <svg class="times-band" viewBox="0 0 590 100" preserveAspectRatio="none" aria-hidden="true">
      <path d="M0 28 L520 10 L586 18 L540 30 L575 38 L500 48 L560 60 L470 72 L555 82 L0 96 Z" fill="#ffffff"/>
    </svg>
    <h2 class="times-label">SHOW TIMES :</h2>

    <div class="times-box"></div>
  </section>
</div>
</body>
</html>
```